Business Card - high end, modern health care

Hey designers!

We need a double sided business card for the boutique, cutting edge physical therapy rehabilitation centre in Sydney's Northern Beaches.

With the most qualified physios in the area The Harbourview Motion Clinic does what other physiotherapy practices do not, we take our time with our patients giving them longer appointments, better physios and therefor faster results!

We guarantee that the service people receive at THMC will be unparalleled.

Hence we need a business card to reflect our modern, boutique, high end service. The final design needs to reflect that we are in a class of our own yet with the feel of beachside retreat.

Below I have attached our logo in both blue on white and white on blue. The exact colour is;
and the font that we have used in our logo is Tex Gyre Aventador.

I like the idea of the blue as the main colour as it is more eye catching and our signage onto the main road will be in this blue and in the interest of consistency across marketing the blue needs to be a part of the design. However I would appreciate a few designs onto a wooden background as this is a visual theme within the fitout of the practice.

The design needs to be of standard size (91x55mm).

Target Market(s)

We target people who have an end outcome in mind and those who have had poor experiences with other providers and ensure that everyone gets the care that they deserve with a premium service that is tailored to the individuals circumstances. As a premium service, the target market is highly educated, business and tech savvy with the additional target market of elderly people who have self funded their retirement and see value in paying for the best ongoing rehabilitation to maintain independence.

Industry/Entity Type

Physical Therapy

Contact Information for Business Card

Name, designation( Titled Musculoskeletal Physiotherapist... there will also be those in the company that have multiple designations ie 5 or 6 words long), phone number, email, facebook, instagram, address

Font styles to use
Sans Serif

Colors

Designer to choose colors to be used in the design.

Requirements
Must have
• Front - The logo as large as possible, blue or wooden theme, and all of the important details.
• Back - A blank space/lines on which to write appointment times (no "Appointment, date, time" etc.)
Nice to have
• facebook url
• logos for facebook and instagram
• Mini logos for the phone and email?

```html
<!DOCTYPE html>
<html lang="en">
<head>
<meta charset="utf-8">
<title>The Harbourview Motion Clinic – Business Card</title>
<link href="https://fonts.googleapis.com/css2?family=Montserrat:wght@400;500;600;700&display=swap" rel="stylesheet">
<style>
  :root {
    --brand-blue: #0f58a8;
    --card-white: #ffffff;
    --ink: #3a3a3a;
    --rule: #8a8a8a;
    --backdrop: #e7e5e2;
  }
  * { box-sizing: border-box; margin: 0; padding: 0; }
  html, body { width: 1200px; height: 930px; overflow: hidden; }
  body {
    background: var(--backdrop);
    font-family: "Montserrat", sans-serif;
    position: relative;
  }
  .card {
    position: absolute;
    width: 560px;
    height: 340px;
    background: var(--card-white);
    border-radius: 16px;
    overflow: hidden;
    box-shadow: 0 10px 30px rgba(0,0,0,.18);
  }
  .card--back { left: 60px; top: 70px; }
  .card--front { left: 580px; top: 520px; }

  /* wordmark */
  .wordmark {
    display: flex;
    align-items: center;
    gap: 12px;
    font-weight: 700;
    text-transform: uppercase;
    line-height: 1.1;
  }
  .wordmark__dot {
    width: 40px; height: 40px; border-radius: 50%;
    flex: none;
  }
  .wordmark__name { font-size: 21px; letter-spacing: .5px; }
  .wordmark__name span { display: block; font-size: 13px; letter-spacing: 4px; }

  /* back */
  .back__band {
    height: 150px;
    background: var(--brand-blue);
    display: flex;
    align-items: center;
    justify-content: center;
  }
  .back__band .wordmark { color: var(--card-white); }
  .back__band .wordmark__dot { background: var(--card-white); }
  .back__label {
    text-align: center;
    color: var(--brand-blue);
    font-size: 14px;
    font-weight: 500;
    margin-top: 18px;
  }
  .back__lines { margin: 14px 70px 0; }
  .back__lines div { border-bottom: 1px solid var(--rule); height: 38px; }

  /* front */
  .front__wave { position: absolute; inset: 0; }
  .front__logo { position: absolute; left: 40px; top: 168px; }
  .front__logo .wordmark { color: var(--brand-blue); }
  .front__logo .wordmark__dot { background: var(--brand-blue); }
  .front__tab {
    position: absolute; right: 0; top: 122px;
    width: 14px; height: 28px; background: var(--brand-blue);
  }
  .front__person { position: absolute; right: 34px; top: 120px; text-align: right; }
  .front__name { color: var(--brand-blue); font-size: 21px; font-weight: 600; }
  .front__title { color: var(--ink); font-size: 12px; margin-top: 2px; }
  .front__rule {
    position: absolute; left: 40px; right: 34px; top: 244px;
    border-top: 1.5px solid var(--brand-blue);
  }
  .front__contact { position: absolute; left: 44px; top: 256px; list-style: none; }
  .front__contact li {
    display: flex; align-items: center; gap: 8px;
    font-size: 13px; color: var(--ink); line-height: 22px;
  }
  .front__contact svg { width: 12px; height: 12px; fill: var(--brand-blue); flex: none; }
  .front__contact .accent { color: var(--brand-blue); }
  .front__address {
    position: absolute; right: 34px; top: 258px;
    text-align: right; font-size: 12px; color: var(--ink); line-height: 19px;
  }
</style>
</head>
<body>

  <section class="card card--back">
    <div class="back__band">
      <div class="wordmark">
        <div class="wordmark__dot"></div>
        <div class="wordmark__name">The Harbourview<span>Motion Clinic</span></div>
      </div>
    </div>
    <p class="back__label">Appointment</p>
    <div class="back__lines"><div></div><div></div><div></div></div>
  </section>

  <section class="card card--front">
    <svg class="front__wave" viewBox="0 0 560 340" preserveAspectRatio="none" aria-hidden="true">
      <path d="M0,0 H560 V50 C510,92 430,108 330,114 C220,120 90,112 0,142 Z" fill="var(--brand-blue)"/>
      <path d="M0,116 C110,88 230,92 330,90 C430,86 510,70 560,36" fill="none" stroke="#fff" stroke-width="3"/>
      <path d="M0,128 C110,100 230,104 330,102 C430,98 510,84 560,54" fill="none" stroke="#fff" stroke-width="1.5"/>
    </svg>

    <div class="front__logo">
      <div class="wordmark">
        <div class="wordmark__dot"></div>
        <div class="wordmark__name">The Harbourview<span>Motion Clinic</span></div>
      </div>
    </div>

    <div class="front__tab"></div>
    <div class="front__person">
      <p class="front__name">DANIEL HART</p>
      <p class="front__title">Director</p>
    </div>

    <div class="front__rule"></div>

    <ul class="front__contact">
      <li><svg viewBox="0 0 24 24"><path d="M6.6 10.8a15 15 0 0 0 6.6 6.6l2.2-2.2a1 1 0 0 1 1-.25 11.4 11.4 0 0 0 3.6.57 1 1 0 0 1 1 1V20a1 1 0 0 1-1 1A17 17 0 0 1 3 4a1 1 0 0 1 1-1h3.5a1 1 0 0 1 1 1c0 1.25.2 2.46.57 3.6a1 1 0 0 1-.25 1z"/></svg><span>+440 1357-2468</span></li>
      <li><svg viewBox="0 0 24 24"><path d="M2 5h20v14H2z M4 7v.5l8 5 8-5V7z" fill-rule="evenodd"/></svg><span>info@harbourview.com</span></li>
      <li><svg viewBox="0 0 24 24"><circle cx="12" cy="12" r="10"/></svg><span>www.<span class="accent">harbourview</span>.com</span></li>
    </ul>

    <p class="front__address">27 Ocean Parade, Unit 4,<br>Seaview Bay, PO 20956</p>
  </section>

</body>
</html>
```